Cabling Business Graphic Design for Website

Hi,

We need a three pages designed for a cabling website: http://www.wirevantage.com.au/

1.) Homepage
2.) Category Page
3.) Product Page

Wirevantage is an online wholesaler of Server Racks and Cables.

Wirevantage began in 2006 as an offshoot of a cabling installation company called Voltrion which has been around since 1993. Through Voltrion and the industry insight that gave use we saw the need for a direct, online wholesaler.

The problem we found the with the industry is the middle man. It seemed that industry suppliers were so obsessed with carving out distribution channels and establishing exclusive resellers and wholesalers that they began to alienate their products and price themselves out of the market.

Then came Wirevantage - the first direct online data comms wholesaler to hit the industry.

We manufacture, import and sell direct - we have no middle men, keep our prices fair and our product range fresh.

Top three competitors:
Summit Kovar - www.pelmor.com.au
Shelfgrid - www.shelfgrid.com.au
Brevinta Communications - www.brevinta.net.au

Our range - we offer a massive range of products - we are always adding new and unique products.

Our Service - we have technical sales staff who are able to help with technical questions and provide advice on how to do things / what to buy - its not just a call centre situation.

We are able to custom manufacture cables and cabinets to suit specifications.

Its very easy to order from us, our turnaround time is 99% of the time 24 hours.

Please refer to the design brief file and the business uncovery for more information. The design brief files are quite specific so please ensure the design adheres to this brief.

Target Market(s)

IT Managers, Electricians, Network Integrators and IT companies.

They have a contract with schools and government departments to order their supplies. This is a massive section of their market.

Industry/Entity Type

Industry

Requirements
Must have
• Reinforce
* that the products adhere to government and industry certifications
* warranty / quality guarantee
* delivery details / stock availability
Nice to have
• Included in the Business Uncovery file
Should not have
• Included in the Business Uncovery

```html
<!DOCTYPE html>
<html lang="en">
<head>
<meta charset="utf-8">
<title>Wirevantage – Home</title>
<link rel="stylesheet" href="https://fonts.googleapis.com/css2?family=Ubuntu:wght@400;500;700&family=Arimo:wght@400;700&display=swap">
<style>
:root{
  --lime:#a6c91a;
  --lime-dark:#7d9a0c;
  --ink:#222;
  --charcoal:#2b2b2b;
  --mist:#e9e9e9;
  --red:#d7141a;
  --blue:#1f86c4;
  --foot-text:#e6e6e6;
}
*{box-sizing:border-box;margin:0;padding:0}
html,body{width:889px;height:1200px;overflow:hidden}
body{position:relative;background:var(--charcoal);font-family:Arimo,Arial,sans-serif;color:var(--ink)}
.abs{position:absolute}

/* header */
.header-band{left:0;top:0;width:889px;height:121px;background:linear-gradient(180deg,#c9e23a 0%,var(--lime) 60%,#9bbd12 100%)}
.login-band{left:0;top:121px;width:889px;height:38px;background:linear-gradient(180deg,#f4f4f4,#dcdcdc)}
.logo-plate{left:0;top:0;width:246px;height:147px;background:#1f1f1f;clip-path:polygon(0 0,246px 0,240px 147px,0 125px)}
.logo-name{left:12px;top:32px;font-family:Ubuntu,sans-serif;font-weight:700;font-size:34px;color:#fff;letter-spacing:-.5px}

.search{left:288px;top:33px;width:343px;height:71px;background:#f3f3f3;border:1px solid #cfcfcf}
.search-label{left:8px;top:12px;font-size:12px;font-weight:700;letter-spacing:.5px;color:#333}
.search-input{left:8px;top:29px;width:228px;height:27px;background:#fff;border:1px solid #c9c9c9;font-size:11px;color:#999;padding:6px 4px;letter-spacing:.5px}
.search-btn{left:251px;top:27px;width:76px;height:31px;border:2px solid #9a9a9a;background:#fff;color:var(--lime-dark);font-weight:700;font-size:12px;text-align:center;line-height:27px;letter-spacing:.4px}

.chat-pill{left:686px;top:21px;width:152px;height:35px;background:var(--lime-dark);border-radius:4px}
.chat-agent{left:670px;top:9px;width:38px;height:48px;border-radius:50% 50% 6px 6px;background:linear-gradient(180deg,#c24c2a,#7a2a16)}
.chat-text{left:713px;top:25px;font-family:Ubuntu,sans-serif;color:#fff;font-size:16px;line-height:15px}
.chat-text small{display:block;font-size:12px;padding-left:50px}
.phone-pill{left:669px;top:77px;width:177px;height:36px;background:var(--lime-dark);border-radius:6px}
.phone-num{left:697px;top:85px;font-family:Ubuntu,sans-serif;color:#fff;font-size:18px}
.phone-icon{left:673px;top:79px}

.field{height:23px;background:#fff;border:1px solid #bdbdbd;font-size:11px;color:#555;padding:5px 8px}
.login-btn{left:776px;top:126px;width:58px;height:26px;background:linear-gradient(#3a3a3a,#111);color:#fff;font-size:12px;font-weight:700;text-align:center;line-height:26px}

/* nav */
.nav{left:5px;top:160px;width:880px;height:44px;background:linear-gradient(180deg,#3a3a3a,#1e1e1e);border:1px solid #111}
.nav-item{top:175px;color:#fff;font-size:10.5px;letter-spacing:0;white-space:nowrap}
.nav-home{left:74px;top:166px;width:69px;height:29px;background:linear-gradient(#c2e034,#8cae0e);border-radius:2px;color:#fff;font-size:10.5px;text-align:center;line-height:29px}
.nav-sep{top:170px;width:1px;height:24px;background:#555}

/* hero */
.hero{left:25px;top:228px;width:842px;height:234px;background:#9a9a9a}
.hero-inner{left:30px;top:232px;width:832px;height:225px;background:linear-gradient(135deg,#f5f5f5,#e4e4e4)}
.hero-mascot{left:55px;top:250px;width:210px;height:197px;background:radial-gradient(ellipse at 45% 55%,#e2463a 0%,#c7322a 45%,#e8e8e8 72%);border-radius:40%}
.hero-cables{left:555px;top:238px;width:307px;height:180px;background:radial-gradient(ellipse at 55% 55%,#2a5db8 0%,#1d47a0 40%,#e6e6e6 75%)}
.hero-line1{left:209px;top:250px;font-family:Ubuntu,sans-serif;font-size:23px;color:#444;line-height:30px}
.hero-line1 .brand{color:var(--lime-dark)}
.hero-line2{left:271px;top:406px;font-family:Ubuntu,sans-serif;font-size:23px;color:#444}
.hero-line2 .accent{color:var(--red)}
.hero-arrow{top:325px}

/* content */
.mist{left:0;top:496px;width:889px;height:433px;background:var(--mist)}
.panel{left:25px;top:475px;width:842px;height:490px;background:linear-gradient(180deg,#f2f2f2,#fff 20%);border:1px solid #ccc}

.cats{left:38px;top:492px;width:171px;height:328px;background:#fff;border:1px solid #ddd}
.cats-title{left:50px;top:500px;font-family:Ubuntu,sans-serif;font-size:16px;font-weight:500;color:var(--blue)}
.cats-list{left:44px;top:527px;width:158px;list-style:none}
.cats-list li{height:21.5px;line-height:21px;font-size:8.6px;color:#333;border-bottom:1px solid #e2e2e2;padding-left:11px;position:relative;white-space:nowrap;overflow:hidden}
.cats-list li::before{content:"";position:absolute;left:1px;top:9px;width:3px;height:3px;background:#777}

.welcome-title{left:226px;top:500px;font-family:Ubuntu,sans-serif;font-size:15.5px;color:var(--lime-dark);font-weight:500}
.welcome-copy{left:226px;top:530px;width:415px;font-size:11px;line-height:18px;letter-spacing:.7px;color:#333;text-align:justify}

.thumb{width:133px;height:98px;background:#2e2e2e;padding:9px}
.thumb span{display:block;width:100%;height:100%}
.thumb-label{font-size:10.5px;font-weight:700;color:#333;text-decoration:underline;letter-spacing:.6px;white-space:nowrap}
.top-title{left:223px;top:782px;font-family:Ubuntu,sans-serif;font-size:16px;color:var(--red)}

.cart-box{left:678px;top:492px;width:171px;height:165px;background:#fff;border:1px solid #ddd}
.cart-head{left:702px;top:495px;width:143px;height:33px;background:#1e1e1e;border-radius:0 6px 6px 0;color:#fff;font-family:Ubuntu,sans-serif;font-weight:500;font-size:12px;line-height:14px;padding:3px 0 0 22px;letter-spacing:.3px}
.cart-icon{left:680px;top:493px;width:36px;height:36px;border-radius:50%;background:#e4471e;border:2px solid #fff}
.cart-art{width:70px;height:68px}
.cart-btn{top:607px;height:23px;background:#1e1e1e;border-radius:3px;color:#fff;font-size:11px;line-height:23px;padding-left:14px}

.mail-box{left:680px;top:678px;width:171px;height:212px;background:#f3f3f3;border:1px solid #ccc}
.mail-head{left:680px;top:678px;width:171px;height:33px;background:linear-gradient(#b8d92a,#8eaf0f);color:#fff;font-family:Ubuntu,sans-serif;font-size:16px;line-height:33px;padding-left:8px}
.mail-copy{left:685px;top:723px;width:110px;font-size:10.5px;line-height:16px;letter-spacing:.5px;color:#333}
.mail-env{left:790px;top:735px;width:52px;height:60px;background:linear-gradient(135deg,#dfeaf6,#2d7fc9);border-radius:8px}
.mail-input{left:689px;top:804px;width:137px;height:22px;background:#fff;border:1px solid #ccc;font-size:10px;color:#888;padding:5px 10px;letter-spacing:.5px}
.mail-btn{left:703px;top:841px;width:66px;height:25px;background:#1e1e1e;border-radius:3px;color:#fff;font-size:13px;font-weight:700;text-align:center;line-height:25px}
.offer-badge{left:799px;top:836px;width:50px;height:50px;border-radius:50%;border:3px solid #e0443f;background:#fbe6e4}

/* footer */
.foot-links{left:0;top:986px;width:889px;text-align:center;font-size:9.5px;color:#fff;white-space:nowrap}
.foot-links span{margin:0 4px}
.foot-rule{left:148px;top:1012px;width:740px;height:1px;background:#3e3e3e}
.foot-head{font-size:10px;font-weight:700;color:var(--lime)}
.foot-head-lg{font-family:Ubuntu,sans-serif;font-size:14px;color:#fff;white-space:nowrap}
.foot-list{font-size:9.5px;line-height:16px;color:var(--foot-text);list-style:none;white-space:nowrap}
.foot-list.bullets li::before{content:"▪ ";font-size:7px}
.foot-photo{left:256px;top:1025px;width:102px;height:94px;background:#fff;border:3px solid var(--lime)}
.foot-photo span{display:block;margin:8px;height:72px;background:radial-gradient(ellipse,#b4b4b4,#eee 70%)}
.foot-note{font-size:9.5px;line-height:12.5px;color:#fff;white-space:nowrap}
</style>
</head>
<body>

<!-- header -->
<div class="abs header-band"></div>
<div class="abs login-band"></div>
<div class="abs logo-plate"></div>
<div class="abs logo-name">Wirevantage</div>

<div class="abs search">
  <div class="abs search-label">SEARCH</div>
  <div class="abs search-input">Search Team.......</div>
  <div class="abs search-btn">SEARCH</div>
</div>

<div class="abs chat-pill"></div>
<div class="abs chat-agent" role="img" aria-label="Headset support agent illustration"></div>
<div class="abs chat-text">LIVE CHAT<small>with us !</small></div>

<div class="abs phone-pill"></div>
<svg class="abs phone-icon" width="22" height="32" viewBox="0 0 22 32" aria-hidden="true"><path d="M5 2 L10 2 L11 9 L8 11 Q9 18 13 23 L16 21 L20 25 L17 30 Q3 24 3 6 Z" fill="#1a1a1a"/></svg>
<div class="abs phone-num">+1(500)987 2210</div>

<div class="abs field" style="left:574px;top:128px;width:85px">Username</div>
<div class="abs field" style="left:682px;top:128px;width:84px">........</div>
<div class="abs login-btn">Login</div>

<!-- nav -->
<div class="abs nav"></div>
<div class="abs nav-home">HOME</div>
<div class="abs nav-sep" style="left:165px"></div>
<div class="abs nav-item" style="left:182px">ABOUT WIREVANTAGE</div>
<div class="abs nav-sep" style="left:310px"></div>
<div class="abs nav-item" style="left:341px">SHIPPING</div>
<div class="abs nav-sep" style="left:424px"></div>
<div class="abs nav-item" style="left:458px">WHOLESALE OUTLETS</div>
<div class="abs nav-sep" style="left:603px"></div>
<div class="abs nav-item" style="left:630px">CHAT WITH US</div>
<div class="abs nav-sep" style="left:737px"></div>
<div class="abs nav-item" style="left:763px">MY ACCOUNT</div>

<!-- hero -->
<div class="abs hero"></div>
<div class="abs hero-inner"></div>
<div class="abs hero-mascot" role="img" aria-label="Illustrated network plug mascot"></div>
<div class="abs hero-cables" role="img" aria-label="Photo of blue network cables with connectors"></div>
<div class="abs hero-line1"><span class="brand">Wirevantage</span> is an Australian owned<br>and operated company.</div>
<div class="abs hero-line2">We <span class="accent">specialise</span> in supplying Voice</div>
<svg class="abs hero-arrow" style="left:36px" width="20" height="40" viewBox="0 0 20 40" aria-hidden="true"><path d="M18 2 L3 20 L18 38" fill="none" stroke="#111" stroke-width="3"/></svg>
<svg class="abs hero-arrow" style="left:833px;top:340px" width="20" height="40" viewBox="0 0 20 40" aria-hidden="true"><path d="M2 2 L17 20 L2 38" fill="none" stroke="#111" stroke-width="3"/></svg>

<!-- content -->
<div class="abs mist"></div>
<div class="abs panel"></div>

<div class="abs cats"></div>
<div class="abs cats-title">Categories <svg width="8" height="10" viewBox="0 0 8 10" aria-hidden="true"><path d="M1 0 L7 5 L1 10Z" fill="#333"/></svg></div>
<ul class="abs cats-list">
  <li>CABLE</li><li>DATA PRODUCTS</li><li>FIBRE PRODUCTS</li><li>COAX PRODUCTS</li>
  <li>ELECTRICAL PRODUCTS</li><li>TELEPHONE / VOICE PRODUCTS</li><li>TOOLS &amp; TESTERS</li>
  <li>COMPUTER CABLES</li><li>SWITCHES &amp; HARDWARE</li><li>AV WALL PLATES &amp; INSERTS</li>
  <li>PLASMA &amp; LCD BRACKETS</li><li>CABLE DUCTING CONDUIT</li><li>SPECIALS</li>
</ul>

<div class="abs welcome-title">Welcome to Wirevantage new Website!!</div>
<p class="abs welcome-copy">Hub Home, a new destination in Orvane Hub 3, provides up‑to‑date information on all your Orvane Studio Suite 3 software in one convenient location. Start Orvane Hub, then click the Hub Home icon at the top of the Favorites panel to access the latest tips, news, and resources for your Studio Suite tools.</p>

<div class="abs thumb" style="left:223px;top:635px"><span role="img" aria-label="Photo of coloured internet patch cables" style="background:linear-gradient(135deg,#f2f2f2,#5a8fd0 45%,#e2c02a 60%,#f2f2f2)"></span></div>
<div class="abs thumb" style="left:367px;top:635px"><span role="img" aria-label="Photo of coiled cable management wrap" style="background:radial-gradient(ellipse,#333 0%,#777 40%,#f0f0f0 70%)"></span></div>
<div class="abs thumb" style="left:511px;top:635px"><span role="img" aria-label="Photo of black data tracking device" style="background:radial-gradient(ellipse,#111 0%,#222 40%,#efefef 70%)"></span></div>
<div class="abs thumb-label" style="left:230px;top:743px">Internet Cable</div>
<div class="abs thumb-label" style="left:373px;top:743px">Cable Management</div>
<div class="abs thumb-label" style="left:523px;top:743px">Data Products</div>

<div class="abs top-title">Top Selling Products <svg width="22" height="16" viewBox="0 0 22 16" aria-hidden="true"><path d="M1 1 L9 8 L1 15 M10 1 L18 8 L10 15" fill="none" stroke="#111" stroke-width="2.5"/></svg></div>
<div class="abs thumb" style="left:222px;top:812px"><span role="img" aria-label="Photo of red and blue network cable plugs" style="background:linear-gradient(90deg,#f1f1f1,#c9302c 35%,#3b6fc4 65%,#f1f1f1)"></span></div>
<div class="abs thumb" style="left:367px;top:812px"><span role="img" aria-label="Photo of HDMI cable connector" style="background:radial-gradient(ellipse,#2a9bd8 0%,#2b2b2b 40%,#efefef 72%)"></span></div>
<div class="abs thumb" style="left:512px;top:812px"><span role="img" aria-label="Photo of coiled black cable" style="background:radial-gradient(ellipse,#555 0%,#2a2a2a 40%,#efefef 72%)"></span></div>
<div class="abs thumb-label" style="left:228px;top:922px">Network Cable</div>
<div class="abs thumb-label" style="left:374px;top:922px">HDMI Cable</div>
<div class="abs thumb-label" style="left:519px;top:922px">Cable</div>

<div class="abs cart-box"></div>
<div class="abs cart-head">Online Shopping<br>Cart ▸▸</div>
<div class="abs cart-icon"></div>
<svg class="abs" style="left:687px;top:502px" width="22" height="18" viewBox="0 0 22 18" aria-hidden="true"><path d="M1 2 H5 L8 12 H18 L20 5 H6" fill="none" stroke="#fff" stroke-width="2"/><circle cx="9" cy="15.5" r="1.6" fill="#fff"/><circle cx="17" cy="15.5" r="1.6" fill="#fff"/></svg>
<div class="abs cart-art" style="left:688px;top:535px;background:radial-gradient(ellipse,#d82424 0%,#3a6ec8 45%,#fff 72%)" role="img" aria-label="Shopping basket illustration"></div>
<div class="abs cart-art" style="left:772px;top:535px;background:linear-gradient(135deg,#e03a8a,#b0155e)" role="img" aria-label="Shopping cart editor software box"></div>
<div class="abs cart-btn" style="left:691px;top:607px;width:70px">View cart</div>
<div class="abs cart-btn" style="left:770px;top:607px;width:70px">Check out</div>

<div class="abs mail-box"></div>
<div class="abs mail-head">Join our mailing lost</div>
<div class="abs mail-copy"><b>Discover</b> exclusive offers, Products Previews and much more...</div>
<div class="abs mail-env" role="img" aria-label="Email envelope illustration"></div>
<div class="abs mail-input">Your Email Address</div>
<div class="abs mail-btn">Submit</div>
<div class="abs offer-badge"></div>

<!-- footer -->
<div class="abs foot-links">
  <span>Home</span>| <span>About Wirevantage</span>| <span>My Account</span>| <span>Order Status</span>| <span>Wish List</span>| <span>Gift Certificate</span>| <span>View Cart</span>| <span>Sign In</span>| <span>An Account</span>
</div>
<div class="abs foot-rule"></div>

<div class="abs foot-head" style="left:72px;top:1027px">FIBRE PRODUCTS</div>
<ul class="abs foot-list" style="left:72px;top:1040px">
  <li>Multimode Fibre Optic Patch Cables</li><li>Single Mode Fibre Optic Patch Leads</li><li>Fibre Optic Cable</li>
</ul>

<div class="abs foot-photo"><span role="img" aria-label="Photo of grey cable with connectors"></span></div>

<div class="abs foot-head-lg" style="left:378px;top:1026px">Advanced Cable</div>
<ul class="abs foot-list bullets" style="left:373px;top:1049px;text-decoration:underline">
  <li>Cat5e Patch Panel</li><li>Cat 6 Patch Panels</li>
</ul>
<div class="abs foot-list" style="left:416px;top:1086px">read more..</div>

<div class="abs foot-head-lg" style="left:550px;top:1026px">About Wirevantage</div>
<ul class="abs foot-list bullets" style="left:545px;top:1048px">
  <li>Multimode Fibre Optic Patch</li><li>Cables Single Mode Fibre</li><li>Optic Patch Leads</li><li>Fibre Optic Cable</li>
</ul>

<div class="abs foot-head" style="left:750px;top:1033px">PATCH PANELS</div>
<ul class="abs foot-list" style="left:750px;top:1047px">
  <li>Cat5e Patch Panel</li><li>Cat 6 Patch Panels</li>
</ul>

<div class="abs foot-note" style="left:25px;top:1155px">Copyright 2010 Wirevantage . Powered By : Brightlane web development<br>SEOBy Netquill Marketing</div>
<div class="abs foot-note" style="left:632px;top:1151px">No. 9, 41 Calder Lane, Marrick, NSW, 2090<br>Telephone: 61 2 9000 3121, Fax: 61 2 9000 3122,<br>E-Mail: sales@wirevantage.com.au ABN #00 111 222 333</div>

</body>
</html>
```